Business Card Design Project

I am looking for a business card design for our online furniture company. Our company name is Plivora Goods, LLC. We sell exquisitely crafted high-end furniture and accessories tailored for a customer base with a wide range of design tastes. We encourage our customers to be creative when decorating the space in which they live and we should have a business card that is representative of that philosophy. A whimsical design is not off limits, but it should not have a look that can be off-putting to male customers. Professional single men are in the market for our products as well as women; therefore, we want a card that is equally appealing to both sexes.

Our card should be as unique as it is creative and should stand apart from typical and often bland business cards. In others words we looking for a card design that will elicit an interaction from other people to help them remember who we are. When a member of our team hands a potential customer our card, we want that person to feel as if they are holding a piece of art. We would like the card to be worthy of conversation unto itself. The card should be visually stimulating in such a way that it will be difficult for recipients to discard, even if they have electronically stored our business information. Keep in mind we will also be giving potential suppliers and interior designers alike our card so it needs to demonstrate that we are a serious and credible business. Both sides of the card can be used for the design if necessary. It may be beneficial for you to consult our website for further inspiration. Please do not hesitate to contact me with any questions you may have over the course of this project.

Industry/Entity Type

Business

Requirements
Must have
• Tobias Keel
Plivora Goods, LLC
Owner/Founder
tkeel@plivoragoods.example
505-418-7394
Design Your Own Space (company slogan, if needed)
www.plivoragoods.example

```html
<!DOCTYPE html>
<html lang="en">
<head>
<meta charset="utf-8">
<title>Plivora Goods – Business Card</title>
<link rel="stylesheet" href="https://fonts.googleapis.com/css2?family=Federo&family=Righteous&family=EB+Garamond:ital,wght@0,600;0,700;1,700&display=swap">
<style>
  :root {
    --brown: #562a18;
    --brown-text: #6b3415;
    --green-light: #bfe37f;
    --green-mid: #8fd05a;
    --green-deep: #3c9a22;
    --brand-green: #a4dc4a;
    --ink: #1e2a12;
    --contact: #56603f;
    --cream: #f7f3e6;
    --rule: #b08a45;
    --white: #ffffff;
    --seat-tone: #3f7a2c;
  }
  * { margin: 0; padding: 0; box-sizing: border-box; }
  html, body {
    width: 1200px; height: 396px; overflow: hidden;
    background: var(--white);
  }
  .sheet { position: relative; width: 1200px; height: 396px; }
  .card {
    position: absolute; top: 15px;
    width: 567px; height: 366px;
    border-radius: 10px; overflow: hidden;
  }
  .card--front { left: 15px; }
  .card--back { left: 618px; }
  .card__art { position: absolute; inset: 0; width: 100%; height: 100%; }

  .brand {
    position: absolute; left: 6px; top: 5px;
    display: flex; align-items: center; gap: 8px;
  }
  .brand__mark {
    width: 38px; height: 38px; background: var(--cream);
    border: 2px solid var(--brown);
  }
  .brand__name {
    font-family: "Righteous", sans-serif; font-size: 27px;
    color: var(--brand-green); line-height: 1;
  }
  .slogan {
    position: absolute; left: 8px; top: 60px; width: 306px;
    font-family: "Federo", serif; font-size: 23px; color: var(--cream);
    word-spacing: 6px; padding-bottom: 6px; white-space: nowrap;
    border-bottom: 1px solid var(--rule);
  }

  .person {
    position: absolute; right: 26px; top: 138px; text-align: right;
    width: 190px;
  }
  .person__name {
    font-family: "Federo", serif; font-size: 29px; color: var(--brown-text);
    line-height: 1.15; white-space: nowrap;
  }
  .person__role {
    font-family: "EB Garamond", serif; font-style: italic; font-weight: 700;
    font-size: 19px; color: var(--brown-text); padding-bottom: 6px;
    border-bottom: 1px solid var(--brown-text);
  }

  .furniture-photo {
    position: absolute; left: 10px; top: 222px; width: 268px; height: 136px;
    background: radial-gradient(ellipse 50% 48% at 50% 52%, #3f7d2e 0%, var(--seat-tone) 55%, rgba(63,122,44,0) 100%);
  }

  .footer-brand {
    position: absolute; right: 22px; bottom: 12px;
    display: flex; align-items: center; gap: 5px;
  }
  .footer-brand__mark { width: 15px; height: 15px; background: var(--ink); }
  .footer-brand__name {
    font-family: "EB Garamond", serif; font-weight: 700; font-size: 18px;
    letter-spacing: 2.5px; color: var(--ink); line-height: 1;
  }

  .contact-band {
    position: absolute; left: 0; right: 0; top: 188px; height: 112px;
    background: rgba(255, 255, 255, 0.28);
  }
  .contact {
    position: absolute; left: 14px; top: 202px;
    font-family: "EB Garamond", serif; font-weight: 700; font-size: 17px;
    color: var(--contact); line-height: 28px; white-space: nowrap;
  }
  .contact__label { margin-right: 8px; }
</style>
</head>
<body>
<div class="sheet">

  <section class="card card--front">
    <svg class="card__art" viewBox="0 0 567 366" preserveAspectRatio="none" aria-hidden="true">
      <defs>
        <linearGradient id="front-green" x1="0" y1="0" x2="0" y2="1">
          <stop offset="0" stop-color="var(--green-light)"/>
          <stop offset="0.55" stop-color="var(--green-mid)"/>
          <stop offset="1" stop-color="var(--green-deep)"/>
        </linearGradient>
      </defs>
      <rect width="567" height="366" fill="url(#front-green)"/>
      <path d="M0,140 C80,200 170,225 260,215 C380,200 470,120 567,70 V120 C470,160 380,230 250,235 C150,238 70,215 0,180 Z" fill="#ffffff" opacity="0.18"/>
      <path d="M0,0 H567 V40 C470,70 380,175 230,172 C130,170 60,140 0,108 Z" fill="var(--brown)"/>
      <path d="M0,108 C60,140 130,170 230,172 C380,175 470,70 567,40" fill="none" stroke="#ffffff" stroke-width="2.5"/>
    </svg>
    <div class="brand">
      <span class="brand__mark"></span>
      <span class="brand__name">Plivora Goods</span>
    </div>
    <div class="slogan">Design Your Own Space</div>
    <div class="person">
      <div class="person__name">Tobias Keel</div>
      <div class="person__role">Owner/Founder</div>
    </div>
    <div class="furniture-photo" role="img" aria-label="Tufted green vintage sofa"></div>
    <div class="footer-brand">
      <span class="footer-brand__mark"></span>
      <span class="footer-brand__name">PlivoraGoods</span>
    </div>
  </section>

  <section class="card card--back">
    <svg class="card__art" viewBox="0 0 567 366" preserveAspectRatio="none" aria-hidden="true">
      <defs>
        <linearGradient id="back-green" x1="0" y1="0" x2="0" y2="1">
          <stop offset="0" stop-color="var(--green-light)"/>
          <stop offset="0.55" stop-color="var(--green-mid)"/>
          <stop offset="1" stop-color="var(--green-deep)"/>
        </linearGradient>
      </defs>
      <rect width="567" height="366" fill="url(#back-green)"/>
      <path d="M0,140 C80,200 170,225 260,215 C380,200 470,120 567,70 V120 C470,160 380,230 250,235 C150,238 70,215 0,180 Z" fill="#ffffff" opacity="0.18"/>
      <path d="M0,0 H567 V40 C470,70 380,175 230,172 C130,170 60,140 0,108 Z" fill="var(--brown)"/>
      <path d="M0,108 C60,140 130,170 230,172 C380,175 470,70 567,40" fill="none" stroke="#ffffff" stroke-width="2.5"/>
    </svg>
    <div class="brand">
      <span class="brand__mark"></span>
      <span class="brand__name">Plivora Goods</span>
    </div>
    <div class="slogan">Design Your Own Space</div>
    <div class="contact-band"></div>
    <div class="contact">
      <div><span class="contact__label">E-mail:</span>tkeel@plivoragoods.example</div>
      <div><span class="contact__label">Tel:</span>505-418-7394</div>
      <div>www.plivoragoods.example</div>
    </div>
    <div class="footer-brand">
      <span class="footer-brand__mark"></span>
      <span class="footer-brand__name">PlivoraGoods</span>
    </div>
  </section>

</div>
</body>
</html>
```